EB-5 Regional Center needs a Web design

Harlow Ridge Financial Partners is an expanding EB-r regional center. We have been successful in sponsoring multiple projects of third-party developers and placing EB-5, B-1, and Private Investments into multiple projects.

We are now partnering directly with project developers in the energy and healthcare to raise foreign capital for projects in those industries. The foreign capital is used as project equity and our collective balance sheets are used to guarantee debt to complete the funding of the projects.

We need a web site where we can post our company credentials, the bios of each partner, a document page for each of our projects where we can post specific project related documents which foreign investors can read, and we will need a section where foreign investors can fill out investor forms confirming that they are qualified investors and leaving their contact so that our agents and executives can make contact.

The final design should reflect the exceptional experience of the partners and our financial strength and stability.

We do have a logo we would want to use on the web design.

Target Market(s)

EB-5 Investors, B-1 Investors, Private Equity and other investors seeking quality investment in job creating US projects.

Coding

Number of Pages Required

5+ page

Font styles to use
Sans Serif

Requirements
Must have
• Pages to display company info, partner bios, projects completed, and a projects in-process page where we can post documents and info on projects for which we are seeking foreign investment. We also need a section where investors can enter their qualifying personal information and leave contact information for us.

```html
<!DOCTYPE html>
<html lang="en">
<head>
<meta charset="utf-8">
<title>Harlow Ridge Financial Partners</title>
<link href="https://fonts.googleapis.com/css2?family=Lora:wght@400;700&family=Montserrat:wght@300;800&family=Open+Sans:wght@400;600;700&display=swap" rel="stylesheet">
<style>
:root{
  --orange:#f26b1d;
  --ink:#222;
  --grey:#666;
  --soft:#ececec;
  --panel:#5b5b5b;
  --black:#0d0d0d;
  --white:#fff;
  --steel:#4a5560;
  --sky:#9fb3c6;
  --paper:#d9dde1;
  --navy:#27313b;
}
*{box-sizing:border-box;margin:0;padding:0}
html,body{width:1200px;height:5020px;overflow:hidden}
body{position:relative;background:var(--white);font-family:"Open Sans",Arial,sans-serif;color:var(--ink)}
.abs{position:absolute}
.btn{position:absolute;background:var(--orange);color:var(--white);font:700 11px/34px "Open Sans",sans-serif;letter-spacing:1px;text-transform:uppercase;padding:0 22px;height:34px;white-space:nowrap;clip-path:polygon(10px 0,calc(100% - 10px) 0,100% 50%,calc(100% - 10px) 100%,10px 100%,0 50%)}
.rule{position:absolute;height:3px;width:54px;background:var(--orange)}
.dot{position:absolute;border-radius:50%}

/* header */
.topbar{position:absolute;left:0;top:0;width:1200px;height:44px;border-bottom:1px solid #e5e5e5;font-size:12px;color:var(--grey);line-height:44px;padding-left:40px}
.topbar .dot{width:20px;height:20px;top:12px;background:#444}
.brand{position:absolute;left:40px;top:60px;display:flex;align-items:center;gap:10px}
.brand .mark{width:36px;height:36px;border-radius:50%;background:#555}
.brand span{font:700 19px/1.1 "Lora",Georgia,serif;color:#333;width:200px}
.nav{position:absolute;right:140px;top:66px;display:flex;gap:26px;font:700 16px "Lora",Georgia,serif;color:#333}
.nav .on{color:var(--orange);border-bottom:2px solid var(--orange);padding-bottom:4px}

/* hero */
.hero{position:absolute;left:0;top:120px;width:1200px;height:760px;
  background:radial-gradient(ellipse at 85% 30%,rgba(255,255,255,.35),transparent 45%),
             radial-gradient(ellipse at 15% 20%,rgba(255,255,255,.45),transparent 40%),
             linear-gradient(120deg,#b5b5b5 0%,#6a6a6a 45%,#2e2e2e 100%)}
.hero-title{position:absolute;left:144px;top:330px;font:800 92px/1 "Montserrat",sans-serif;color:var(--white);letter-spacing:2px}
.hero-sub{position:absolute;left:146px;top:432px;font:300 42px/1 "Montserrat",sans-serif;color:var(--white);letter-spacing:7px}
.hero-lead{position:absolute;left:146px;top:486px;font:700 17px "Open Sans",sans-serif;color:var(--white)}
.slider .dot{width:9px;height:9px;left:1136px;background:rgba(255,255,255,.6)}

/* about */
.about-art{position:absolute;left:90px;top:920px;width:360px;height:420px;
  background:radial-gradient(circle at 30% 30%,#e9e3da,transparent 55%),linear-gradient(135deg,#b7c2cc,#4e5863)}
.about h2{position:absolute;left:600px;top:930px;font:700 46px "Lora",Georgia,serif}
.about h3{position:absolute;left:600px;top:994px;font:400 26px "Lora",Georgia,serif;color:#333}
.about p{position:absolute;left:600px;top:1060px;width:480px;font-size:14px;line-height:1.75;color:var(--grey)}

/* services */
.cell{position:absolute;width:400px;height:326px}
.photo-a{background:radial-gradient(circle at 40% 40%,#8fb4d6,transparent 60%),linear-gradient(135deg,#5d7487,var(--navy))}
.photo-b{background:radial-gradient(circle at 60% 50%,#c9b8a4,transparent 55%),linear-gradient(135deg,#3a3f44,#8d979f)}
.photo-c{background:radial-gradient(circle at 50% 40%,#f4f6f8,transparent 60%),linear-gradient(135deg,var(--paper),#7f8a94)}
.photo-d{background:radial-gradient(circle at 55% 45%,#6fd0c8,transparent 45%),linear-gradient(135deg,#2d3a44,#121820)}
.service{background:var(--panel);color:var(--white);text-align:center}
.service svg{margin-top:40px}
.service h4{font:700 21px "Lora",Georgia,serif;margin-top:10px}
.service p{font-size:12px;line-height:1.6;width:260px;margin:10px auto 0;color:#e8e8e8}
.service .btn{left:148px;top:252px;height:28px;line-height:28px;font-size:10px}

/* section heads */
.head{position:absolute;left:0;width:1200px;text-align:center;font:400 40px "Lora",Georgia,serif;color:#555}
.head b{color:var(--ink)}

/* team */
.member{position:absolute;width:220px;text-align:center}
.diamond{width:220px;height:220px;position:relative}
.diamond .frame{position:absolute;left:32px;top:32px;width:156px;height:156px;transform:rotate(45deg);border:1px solid #bbb;background:var(--white)}
.diamond .pic{position:absolute;left:46px;top:46px;width:128px;height:128px;transform:rotate(45deg)}
.pic.p1{background:linear-gradient(135deg,#dfe6ee,#2f4c7a)}
.pic.p2{background:linear-gradient(135deg,#e8e2dc,#5a4a44)}
.pic.p3{background:linear-gradient(135deg,#f2f2f0,#8c9aa6)}
.pic.p4{background:linear-gradient(135deg,#f1d9b5,#c78a2c)}
.member h5{font:700 18px "Lora",Georgia,serif;margin-top:14px}
.member p{font-size:12px;line-height:1.6;color:var(--grey);margin-top:8px}
.socials{display:flex;justify-content:center;gap:12px;margin-top:10px}
.socials i{width:12px;height:12px;border-radius:50%;background:#444;display:block}

/* projects */
.projects{position:absolute;left:0;top:2948px;width:1200px;height:892px;background:var(--soft)}
.tile{position:absolute;width:298px;height:222px}

/* contact */
.contact{position:absolute;left:0;top:3840px;width:1200px;height:940px;background:linear-gradient(180deg,#474747,#2b2b2b)}
.contact h2{position:absolute;left:144px;top:108px;font:400 40px "Lora",Georgia,serif;color:#ddd}
.contact h2 b{color:var(--white)}
.contact .intro{position:absolute;left:144px;top:188px;width:400px;font-size:13px;line-height:1.6;color:#ccc}
.field{position:absolute;left:144px;width:400px;border-bottom:1px solid #8a8a8a;font-size:13px;color:#ccc;padding-bottom:14px}
.contact-photo{position:absolute;left:640px;top:100px;width:416px;height:300px;
  background:radial-gradient(ellipse at 50% 0%,#dbe8f4,transparent 55%),linear-gradient(160deg,var(--sky),#2c3845)}
.info h6{position:absolute;left:640px;font:600 16px "Open Sans",sans-serif;letter-spacing:2px;color:var(--white)}
.info p{position:absolute;left:640px;font-size:13px;line-height:1.5;color:#ccc;width:280px}

/* footer */
.footer{position:absolute;left:0;top:4780px;width:1200px;height:240px;background:var(--black);color:#bbb;text-align:center}
.footer .ring{width:30px;height:30px;border:2px solid #ccc;border-radius:50%;display:inline-block;margin:0 5px}
.footer .line{font-size:12px;margin-top:20px}
.footer hr{border:0;border-top:1px solid #333;margin:18px 0 0}
.footer nav{display:flex;justify-content:center;gap:26px;font:700 14px "Open Sans",sans-serif;color:var(--white);margin-top:18px;letter-spacing:1px}
.footer small{display:block;font-size:11px;margin-top:18px;color:#999}
</style>
</head>
<body>

<header>
  <div class="topbar">Phone : 1-800-555-0142 &nbsp;|&nbsp; Email : info@harlowridgefinancial.com
    <span class="dot" style="left:930px"></span><span class="dot" style="left:958px"></span><span class="dot" style="left:986px"></span><span class="dot" style="left:1014px"></span>
  </div>
  <div class="brand"><div class="mark"></div><span>Harlow Ridge Financial Partners</span></div>
  <nav class="nav"><span class="on">Home</span><span>About</span><span>Services</span><span>Projects</span><span>Team</span><span>Contact</span></nav>
</header>

<section class="hero" role="img" aria-label="Photo of analysts reviewing stock charts on laptops"></section>
<div class="hero-title">HARLOW RIDGE</div>
<div class="hero-sub">Financial Partners</div>
<div class="hero-lead">EB-5 capital for job-creating US energy and healthcare projects</div>
<div class="btn" style="left:144px;top:535px">Get Started ➜</div>
<div class="slider"><span class="dot" style="top:400px"></span><span class="dot" style="top:418px;background:#fff"></span><span class="dot" style="top:436px"></span><span class="dot" style="top:454px"></span></div>
<svg class="abs" style="left:0;top:740px" width="1200" height="160" viewBox="0 0 1200 160">
  <polygon points="0,30 600,122 1200,30 1200,160 0,160" fill="#fff"/>
  <circle cx="600" cy="92" r="28" fill="#fff" stroke="#555" stroke-width="4"/>
</svg>

<section class="about">
  <div class="about-art" role="img" aria-label="Collage of partners meeting with investors"></div>
  <h2>ABOUT</h2>
  <h3>Harlow Ridge Financial Partners</h3>
  <div class="rule" style="left:600px;top:1040px"></div>
  <p>We sponsor EB-5, B-1 and private investment in vetted US projects. Partnering directly with developers in energy and healthcare, we place foreign capital as project equity while our collective balance sheets guarantee the debt that completes each funding stack. Our partners bring decades of experience, financial strength and steady stewardship to every investor we serve.</p>
  <div class="btn" style="left:600px;top:1296px">Read More ➜</div>
</section>

<section class="services">
  <div class="cell photo-a" style="left:0;top:1468px" role="img" aria-label="Photo of a laptop showing financial charts"></div>
  <div class="cell service" style="left:400px;top:1468px">
    <svg width="54" height="54" viewBox="0 0 54 54" fill="none" stroke="#fff" stroke-width="3"><circle cx="22" cy="22" r="15"/><line x1="33" y1="33" x2="48" y2="48"/><polyline points="13,27 19,20 24,24 31,15"/></svg>
    <h4>Market Research</h4>
    <p>We vet every developer, market and job-creation model before any project reaches our investors.</p>
    <div class="btn">Read More ➜</div>
  </div>
  <div class="cell photo-d" style="left:800px;top:1468px" role="img" aria-label="Photo of a hand holding a phone with a trading chart"></div>
  <div class="cell service" style="left:0;top:1794px">
    <svg width="54" height="54" viewBox="0 0 54 54" fill="none" stroke="#fff" stroke-width="3"><circle cx="20" cy="20" r="12"/><circle cx="36" cy="34" r="12"/><line x1="20" y1="14" x2="20" y2="26"/><line x1="36" y1="28" x2="36" y2="40"/></svg>
    <h4>Investment Management</h4>
    <p>Foreign capital placed as project equity, backed by our guarantee on completion debt.</p>
    <div class="btn">Read More ➜</div>
  </div>
  <div class="cell photo-c" style="left:400px;top:1794px" role="img" aria-label="Photo of hands reviewing printed charts with a pen"></div>
  <div class="cell service" style="left:800px;top:1794px">
    <svg width="54" height="54" viewBox="0 0 54 54" fill="none" stroke="#fff" stroke-width="3"><line x1="6" y1="48" x2="48" y2="48"/><rect x="10" y="30" width="8" height="18"/><rect x="23" y="20" width="8" height="28"/><rect x="36" y="10" width="8" height="38"/></svg>
    <h4>Sales &amp; Trading</h4>
    <p>Project documents, filings and progress reports posted for qualified investors to review.</p>
    <div class="btn">Read More ➜</div>
  </div>
</section>

<section class="team">
  <div class="head" style="top:2220px"><b>OUR</b> Team</div>
  <div class="rule" style="left:573px;top:2296px"></div>
  <div class="member" style="left:142px;top:2380px"><div class="diamond"><div class="frame"></div><div class="pic p1" role="img" aria-label="Portrait of managing partner"></div></div><h5>John Doe</h5><p>Managing Partner,<br>EB-5 program lead</p><div class="socials"><i></i><i></i></div></div>
  <div class="member" style="left:380px;top:2380px"><div class="diamond"><div class="frame"></div><div class="pic p2" role="img" aria-label="Portrait of compliance partner"></div></div><h5>Mira Castell</h5><p>Partner,<br>investor compliance</p><div class="socials"><i></i><i></i></div></div>
  <div class="member" style="left:618px;top:2380px"><div class="diamond"><div class="frame"></div><div class="pic p3" role="img" aria-label="Portrait of energy projects partner"></div></div><h5>Devan Roy</h5><p>Partner,<br>energy projects</p><div class="socials"><i></i><i></i></div></div>
  <div class="member" style="left:856px;top:2380px"><div class="diamond"><div class="frame"></div><div class="pic p4" role="img" aria-label="Portrait of healthcare projects partner"></div></div><h5>Aliquip</h5><p>Partner,<br>healthcare projects</p><div class="socials"><i></i><i></i></div></div>
  <div class="btn" style="left:530px;top:2806px">View More ➜</div>
</section>

<section class="projects">
  <div class="head" style="top:92px"><b>OUR</b> Projects</div>
  <div class="rule" style="left:573px;top:168px"></div>
  <div class="tile photo-a" style="left:144px;top:232px" role="img" aria-label="Project photo: energy project financial charts"></div>
  <div class="tile photo-c" style="left:451px;top:232px" role="img" aria-label="Project photo: project offering documents"></div>
  <div class="tile photo-c" style="left:758px;top:232px" role="img" aria-label="Project photo: laptop with project report"></div>
  <div class="tile photo-b" style="left:144px;top:462px" role="img" aria-label="Project photo: developer meeting"></div>
  <div class="tile photo-d" style="left:451px;top:462px" role="img" aria-label="Project photo: healthcare project charts"></div>
  <div class="tile photo-a" style="left:758px;top:462px" role="img" aria-label="Project photo: analyst reviewing investment data"></div>
  <div class="btn" style="left:530px;top:750px">View More ➜</div>
</section>

<section class="contact">
  <h2><b>CONTACT</b> Form</h2>
  <div class="rule" style="left:144px;top:166px"></div>
  <p class="intro">Confirm you are a qualified investor and our agents will contact you.</p>
  <div class="field" style="top:270px">Enter Name</div>
  <div class="field" style="top:350px">Enter Email</div>
  <div class="field" style="top:430px">Phone</div>
  <div class="field" style="top:510px;height:100px">Message</div>
  <div class="btn" style="left:144px;top:730px;height:40px;line-height:40px">Submit Message ➜</div>
  <div class="contact-photo" role="img" aria-label="Photo looking up at glass office towers"></div>
  <div class="info">
    <h6 style="top:430px">ADDRESS</h6><p style="top:460px">123 Ridge Avenue, Suite 400,<br>Austin, TX 78701</p>
    <h6 style="top:540px">PHONE</h6><p style="top:570px">1-800-555-0142</p>
    <h6 style="top:640px">EMAIL</h6><p style="top:670px">info@harlowridgefinancial.com</p>
  </div>
  <svg class="abs" style="left:570px;top:820px" width="60" height="60"><circle cx="30" cy="30" r="24" fill="none" stroke="#fff" stroke-width="4"/></svg>
</section>

<footer class="footer">
  <div style="margin-top:20px"><span class="ring"></span><span class="ring"></span><span class="ring"></span><span class="ring"></span><span class="ring"></span></div>
  <div class="line">123 Ridge Avenue, Austin, TX &nbsp;&nbsp;|&nbsp;&nbsp; Phone : 1-800-555-0142 &nbsp;&nbsp;|&nbsp;&nbsp; info@harlowridgefinancial.com</div>
  <hr>
  <nav><span>HOME</span><span>ABOUT</span><span>SERVICES</span><span>PROJECTS</span><span>TEAM</span><span>CONTACT</span></nav>
  <small>© 2018 Harlow Ridge Financial Partners - All Rights Reserved. Privacy policy</small>
</footer>

</body>
</html>
```